Marcus Delbridge Finance

Need a personal website advertising Equipment Finance,Business Finance,Commercial Finance, Construction Finance, Bridging Finance. Similar websites are www.corvalend.com.au / www.tarmivest.com.au / www.qbr7.com.au /wwwhalvecredit.com.au

Target Market(s)

Business People

Industry/Entity Type

Business

Number of Pages Required

3 page

Font styles to use
Serif
Sans Serif

Requirements
Must have
• All i want is a simple corporate looking website advertising Equipment Finance, Commercial Finance, Construction Finance, Business Finance, Bridging Finance,

```html
<!DOCTYPE html>
<html lang="en">
<head>
<meta charset="utf-8">
<title>Marcus Delbridge Finance</title>
<link href="https://fonts.googleapis.com/css2?family=Oswald:wght@400;500&family=Open+Sans:ital,wght@0,400;0,600;1,400&display=swap" rel="stylesheet">
<style>
:root{
  --navy:#0e4677;
  --navy-deep:#0b3d6b;
  --sky:#22b3e2;
  --sky-dark:#1a9fd0;
  --ink:#333;
  --muted:#666;
  --light:#f0f0f0;
  --line:#d8d8d8;
  --footer:#1e1e1e;
  --white:#fff;
  --star:#f2c618;
}
*{box-sizing:border-box;margin:0;padding:0}
html,body{width:1200px;height:2233px;overflow:hidden;background:var(--white)}
body{font-family:'Open Sans',Arial,sans-serif;color:var(--ink);position:relative}

/* header */
.site-header{position:absolute;left:0;top:0;width:1200px;height:122px;background:var(--white)}
.brand{position:absolute;left:92px;top:30px;display:flex;align-items:center;gap:12px}
.brand-dot{width:58px;height:58px;border-radius:50%;background:var(--sky);flex:none}
.brand-name{font-family:'Oswald',sans-serif;font-weight:500;font-size:30px;color:var(--navy);line-height:1}
.header-contact{position:absolute;right:88px;top:28px;text-align:right;color:#222}
.header-phone{font-size:29px;display:flex;align-items:center;gap:12px;justify-content:flex-end;line-height:1.1}
.header-email{font-size:21px;margin-top:2px}

/* nav */
.main-nav{position:absolute;left:0;top:122px;width:1200px;height:60px;background:var(--sky)}
.main-nav a{position:absolute;top:0;height:60px;line-height:60px;color:var(--white);font-size:16px;text-decoration:none;text-transform:uppercase}
.main-nav a.active{background:var(--navy);width:134px;text-align:center}

/* hero */
.hero{position:absolute;left:0;top:182px;width:1200px;height:522px;background:linear-gradient(120deg,#5b5650 0%,#8d8478 35%,#a7a08f 55%,#6f6a60 80%,#4a4640 100%)}
.hero-title{position:absolute;left:89px;top:228px;font-family:'Oswald',sans-serif;color:var(--white);line-height:1}
.hero-title h1{font-weight:500;font-size:56px;letter-spacing:.5px}
.hero-title p{font-weight:400;font-size:31px;margin-top:12px}
.slider-arrows{position:absolute;left:89px;top:352px;display:flex;gap:6px}
.slider-arrows span{width:30px;height:30px;border-radius:50%;background:rgba(0,0,0,.55);display:flex;align-items:center;justify-content:center}
.lead-form{position:absolute;left:808px;top:93px;width:306px;height:365px;background:rgba(14,62,104,.88);padding:24px 26px}
.lead-form h2{font-family:'Oswald',sans-serif;font-weight:400;font-size:26px;color:var(--white);text-align:center;letter-spacing:.5px;margin-bottom:14px}
.field{height:45px;background:var(--white);margin-bottom:8px;font-size:13px;color:#333;padding:0 14px;display:flex;align-items:center;justify-content:space-between}
.submit{height:45px;background:var(--sky);color:var(--white);font-weight:600;font-size:16px;display:flex;align-items:center;justify-content:center;margin-top:4px}

/* welcome */
.section-title{position:absolute;left:0;width:1200px;text-align:center;color:var(--navy);font-size:27px;font-weight:400}
.welcome-title{top:757px;font-weight:600;font-size:28px}
.welcome-text{position:absolute;left:112px;top:806px;width:976px;text-align:center;font-size:12.5px;line-height:21px;color:#555}
.services{position:absolute;left:89px;top:938px;width:1022px;height:171px;display:flex;border:1px solid var(--line)}
.service{flex:1;display:flex;flex-direction:column;align-items:center;padding-top:34px;border-right:1px solid var(--line)}
.service:last-child{border-right:none}
.service.shade{background:var(--light)}
.service-icon{height:54px;display:flex;align-items:flex-end;justify-content:center}
.service span{margin-top:22px;font-size:17px;color:#222;text-transform:uppercase}

/* what we do */
.what-we-do{position:absolute;left:0;top:1155px;width:1200px;height:460px;background:var(--light)}
.what-title{top:1197px}
.card{position:absolute;top:1267px;width:316px}
.card-img{height:192px;border:1px solid #ddd}
.card h3{font-size:16px;font-weight:400;color:#222;margin-top:20px}
.card p{font-size:13px;line-height:19px;color:#777;margin-top:6px}
.card a{display:block;font-size:13px;color:var(--sky);text-decoration:none;margin-top:6px}

/* testimonials */
.testimonials-title{top:1678px}
.testimonial{position:absolute;top:1748px;width:460px;height:130px}
.avatar{position:absolute;left:0;top:0;width:92px;height:92px;border-radius:50%;background:linear-gradient(160deg,#c9a58d,#7d5a48)}
.quote{position:absolute;left:112px;top:0;width:330px}
.quote q{display:block;font-style:italic;font-size:12px;line-height:22px;color:#444;quotes:none;padding-left:22px;position:relative}
.quote-mark{position:absolute;font-family:Georgia,serif;font-size:34px;color:#aaa;line-height:1}
.who{font-size:12px;color:#333;margin-top:6px;padding-left:22px}
.who b{font-weight:600;text-transform:uppercase;font-size:11px;margin-right:6px}
.stars{display:flex;gap:3px;margin-top:6px;padding-left:20px}

/* footer */
.site-footer{position:absolute;left:0;top:1941px;width:1200px;height:292px;background:var(--footer);color:var(--white)}
.footer-brand{position:absolute;left:89px;top:94px;display:flex;align-items:center;gap:10px;width:260px}
.footer-brand .brand-dot{width:50px;height:50px}
.footer-brand .brand-name{color:var(--white);font-size:24px;line-height:1.1;width:190px}
.footer-col{position:absolute;top:56px}
.footer-col h4{font-size:15px;font-weight:400;text-transform:uppercase;margin-bottom:16px}
.footer-col p{font-size:11.5px;line-height:21px}
.mail-row{display:flex;margin-top:16px}
.mail-row span{height:30px;display:flex;align-items:center;font-size:11px;padding:0 10px}
.mail-input{width:146px;background:var(--white);color:#888}
.mail-btn{background:var(--sky);color:var(--white)}
.social{display:flex;gap:13px}
.social span{width:24px;height:24px;border-radius:4px;background:var(--white)}
.footer-rule{position:absolute;left:82px;top:221px;width:1022px;height:1px;background:#3a3a3a}
.copyright{position:absolute;left:0;top:246px;width:1200px;text-align:center;font-size:12px}
</style>
</head>
<body>

<header class="site-header">
  <div class="brand">
    <span class="brand-dot"></span>
    <span class="brand-name">Marcus Delbridge Finance</span>
  </div>
  <div class="header-contact">
    <div class="header-phone">
      <svg width="22" height="22" viewBox="0 0 22 22"><rect width="22" height="22" rx="3" fill="#22b3e2"/><path d="M7 5c1 0 1.6 2.2 1.8 3 .2.8-1 1.2-.8 1.9.5 1.4 2 2.9 3.4 3.4.7.2 1.1-1 1.9-.8.8.2 3 .8 3 1.8 0 1.2-1.3 2.2-2.6 2.2C9 16.5 5.5 13 5.5 8 5.5 6.300 6 5 7 5z" fill="#fff"/></svg>
      61 7 5580 2714
    </div>
    <div class="header-email">info@marcusdelbridge.com</div>
  </div>
</header>

<nav class="main-nav">
  <a class="active" style="left:89px">Home</a>
  <a style="left:256px">About Us</a>
  <a style="left:407px">Services</a>
  <a style="left:550px">Finance</a>
  <a style="left:692px">Supports</a>
  <a style="left:840px">Apply Now</a>
  <a style="left:1006px">Contact</a>
</nav>

<section class="hero" role="img" aria-label="Hands cupping a pile of coins with a young green seedling growing from them">
  <div class="hero-title">
    <h1>BUSINESS FINANCE</h1>
    <p>FINANCE INDUSTRY IN AUSTRALIA</p>
  </div>
  <div class="slider-arrows">
    <span><svg width="10" height="12" viewBox="0 0 10 12"><path d="M7 1 2 6l5 5" stroke="#fff" stroke-width="2" fill="none"/></svg></span>
    <span><svg width="10" height="12" viewBox="0 0 10 12"><path d="M3 1l5 5-5 5" stroke="#fff" stroke-width="2" fill="none"/></svg></span>
  </div>
  <form class="lead-form">
    <h2>LET'S GET STARTED</h2>
    <div class="field">Name</div>
    <div class="field">Email</div>
    <div class="field">Phone</div>
    <div class="field">Type of Finance <svg width="10" height="6" viewBox="0 0 10 6"><path d="M0 0h10L5 6z" fill="#111"/></svg></div>
    <div class="submit">SUBMIT</div>
  </form>
</section>

<h2 class="section-title welcome-title">WELCOME TO MARCUS DELBRIDGE FINANCE</h2>
<p class="welcome-text">Mr. Marcus Delbridge serves as Operations Director of Harlow Crest Financial Services Pty Ltd. Mr. Delbridge has 16 years experience in the Financial Services and bridging Finance industry, both in Australia, as well as in South Africa. He was employed by the South African based business (MERIDIAN PLAINS FINANCE) for the majority of its operation. He held senior operational positions within Meridian Plains Finance and provided staff support and direction, training and operational control for the Company. Since the establishment of Harlow Crest Financial Services, Mr. Delbridge has implemented constant Procedures, Policy and system</p>

<div class="services">
  <div class="service shade">
    <div class="service-icon"><svg width="60" height="48" viewBox="0 0 60 48"><path d="M12 8h36l6 16v18h-8v-6H14v6H6V24z" fill="#22b3e2"/><path d="M16 12h28l4 11H12z" fill="#f0f0f0"/><circle cx="15" cy="30" r="4" fill="#f0f0f0"/><circle cx="45" cy="30" r="4" fill="#f0f0f0"/></svg></div>
    <span>Equipment Finance</span>
  </div>
  <div class="service">
    <div class="service-icon"><svg width="56" height="52" viewBox="0 0 56 52"><circle cx="28" cy="11" r="9" fill="#22b3e2"/><circle cx="10" cy="17" r="6.5" fill="#22b3e2"/><circle cx="46" cy="17" r="6.5" fill="#22b3e2"/><path d="M14 52V34a14 14 0 0 1 28 0v18z" fill="#22b3e2"/><path d="M0 44V32a10 10 0 0 1 15-8v20zM56 44V32a10 10 0 0 0-15-8v20z" fill="#22b3e2"/></svg></div>
    <span>Business Finance</span>
  </div>
  <div class="service shade">
    <div class="service-icon"><svg width="56" height="50" viewBox="0 0 56 50"><path d="M28 0 56 12H0z" fill="#22b3e2"/><rect x="2" y="14" width="52" height="4" fill="#22b3e2"/><rect x="7" y="20" width="6" height="20" fill="#22b3e2"/><rect x="19" y="20" width="6" height="20" fill="#22b3e2"/><rect x="31" y="20" width="6" height="20" fill="#22b3e2"/><rect x="43" y="20" width="6" height="20" fill="#22b3e2"/><rect x="2" y="42" width="52" height="8" fill="#22b3e2"/></svg></div>
    <span>Commercial Finance</span>
  </div>
  <div class="service">
    <div class="service-icon"><svg width="40" height="52" viewBox="0 0 40 52"><rect width="40" height="52" fill="#22b3e2"/><g fill="#fff"><rect x="6" y="6" width="7" height="6"/><rect x="17" y="6" width="7" height="6"/><rect x="28" y="6" width="7" height="6"/><rect x="6" y="16" width="7" height="6"/><rect x="17" y="16" width="7" height="6"/><rect x="28" y="16" width="7" height="6"/><rect x="6" y="26" width="7" height="6"/><rect x="17" y="26" width="7" height="6"/><rect x="28" y="26" width="7" height="6"/><rect x="15" y="38" width="10" height="14"/></g></svg></div>
    <span>Construction Finance</span>
  </div>
</div>

<section class="what-we-do"></section>
<h2 class="section-title what-title">WHAT WE DO</h2>
<article class="card" style="left:92px">
  <div class="card-img" role="img" aria-label="Business people reviewing charts and reports on a desk" style="background:linear-gradient(135deg,#c9a47c,#e6e9ee 55%,#7f93b0)"></div>
  <h3>Lorem ipsum dolor sit amet,</h3>
  <p>Lorem ipsum dolor sit amet, consectetur adipiscing elit. Sed blandit massa vel mauris sollicitudin dignis-</p>
  <a>Read More -&gt;</a>
</article>
<article class="card" style="left:444px">
  <div class="card-img" role="img" aria-label="Collage of coins, circuit board, world map and city towers" style="background:linear-gradient(135deg,#8a7a6c,#3f86c4 50%,#b43a3a)"></div>
  <h3>Lorem ipsum dolor sit amet,</h3>
  <p>Lorem ipsum dolor sit amet, consectetur adipiscing elit. Sed blandit massa vel mauris sollicitudin dignis-</p>
  <a>Read More -&gt;</a>
</article>
<article class="card" style="left:798px">
  <div class="card-img" role="img" aria-label="Stacks of gold coins on financial papers" style="background:linear-gradient(180deg,#f6f6f4,#e4d9bb 55%,#c9a24a)"></div>
  <h3>Lorem ipsum dolor sit amet,</h3>
  <p>Lorem ipsum dolor sit amet, consectetur adipiscing elit. Sed blandit massa vel mauris sollicitudin dignis-</p>
  <a>Read More -&gt;</a>
</article>

<h2 class="section-title testimonials-title">OUR CUSTOMERS SAY</h2>
<div class="testimonial" style="left:104px">
  <div class="avatar" role="img" aria-label="Portrait photo of a smiling female customer"></div>
  <div class="quote">
    <span class="quote-mark" style="left:0;top:-4px">&ldquo;</span>
    <q>Lorem Ipsum has been the industry's standard dummy text ever since the 1500s, when an unknown printer took a galley of type and scrambled it to make</q>
    <div class="who"><b>Leon Hartley</b>Marketing Executive</div>
    <div class="stars">
      <svg width="120" height="22" viewBox="0 0 120 22"><g fill="#f2c618"><path id="st" d="M11 1l3 7h7.5l-6 4.6 2.3 7.4L11 15.6 4.2 20l2.3-7.4-6-4.6H8z"/><use href="#st" x="24"/><use href="#st" x="48"/><use href="#st" x="72"/><use href="#st" x="96"/></g></svg>
    </div>
  </div>
</div>
<div class="testimonial" style="left:658px">
  <div class="avatar" role="img" aria-label="Portrait photo of a smiling male customer" style="background:linear-gradient(160deg,#e0c3a8,#6d5446)"></div>
  <div class="quote">
    <span class="quote-mark" style="left:0;top:-4px">&ldquo;</span>
    <q>Lorem Ipsum has been the industry's standard dummy text ever since the 1500s, when an unknown printer took a galley of type and scrambled it to make</q>
    <div class="who"><b>Leon Hartley</b>Marketing Executive</div>
    <div class="stars">
      <svg width="120" height="22" viewBox="0 0 120 22"><g fill="#f2c618"><use href="#st"/><use href="#st" x="24"/><use href="#st" x="48"/><use href="#st" x="72"/><use href="#st" x="96"/></g></svg>
    </div>
  </div>
</div>

<footer class="site-footer">
  <div class="footer-brand">
    <span class="brand-dot"></span>
    <span class="brand-name">Marcus Delbridge Finance</span>
  </div>
  <div class="footer-col" style="left:375px">
    <h4>Contact Us</h4>
    <p>Address : 14 Coral Parade Harbour<br>&nbsp;Point, Queensland 4218, Australia</p>
    <p style="margin-top:4px">Phone: 61 7 5580 2714</p>
    <p style="margin-top:4px">Fax: 61 7 5580 2790</p>
    <p style="margin-top:4px">Email : info@marcusdelbridge.com</p>
  </div>
  <div class="footer-col" style="left:676px">
    <h4>Join Our Mailing List</h4>
    <p style="width:200px;line-height:18px">Your about us information would fit here nicely.</p>
    <div class="mail-row"><span class="mail-input">Email address</span><span class="mail-btn">Submit</span></div>
  </div>
  <div class="footer-col" style="left:948px">
    <h4>Follow Us Out There</h4>
    <div class="social"><span></span><span></span><span></span><span></span></div>
  </div>
  <div class="footer-rule"></div>
  <p class="copyright">Copyright © 2017. All Rights Reserved</p>
</footer>

</body>
</html>
```